Design a Low Carb High Protein Chips Bag

Hello,

Our client is launching a brand new Low Carb snack product. It is a Chips product that is high in protein and low in carbohydrates. There are similar products on the market but this bag is 80 grams so much bigger and the product is very tasty.

The flavor will be sour cream.

Your job is to design the bag. If you are chosen as the winner you will finalize the bag with ingredients, nutrition, and so on. You will be given a cutters guide. To get inspired you can check the client's home page at munchvale.co.uk.

```html
<!DOCTYPE html>
<html lang="en">
<head>
<meta charset="utf-8">
<title>Munchvale Low Carb Chips – Bag Front</title>
<link href="https://fonts.googleapis.com/css2?family=Kaushan+Script&family=Oswald:wght@500;600&family=Playfair+Display:wght@400;700;900&display=swap" rel="stylesheet">
<style>
  :root {
    --backdrop: #f1c873;
    --bag-white: #f3f3f3;
    --brand-red: #c9415a;
    --heart-red: #cf4b64;
    --ink: #161616;
    --gold: #f6c431;
    --chip-light: #f6dc8a;
    --chip-deep: #d9a93c;
    --carbs-green: #b3c84a;
    --fat-teal: #7cc2c0;
    --sugar-gold: #d6b03f;
  }
  * { box-sizing: border-box; margin: 0; padding: 0; }
  html, body { width: 1200px; height: 1020px; overflow: hidden; }
  body { background: var(--backdrop); position: relative; font-family: "Oswald", sans-serif; }

  .bag {
    position: absolute; left: 220px; top: 50px; width: 760px; height: 920px;
    background: var(--bag-white); border-radius: 10px; overflow: hidden;
  }
  .bag-pattern { position: absolute; inset: 0; background: var(--bag-white); }

  .brand-tab {
    position: absolute; left: 210px; top: 0; width: 340px; height: 110px;
    background: var(--brand-red); border-radius: 0 0 8px 8px;
    display: flex; align-items: center; justify-content: center;
  }
  .brand-name { color: #fff; font: 500 40px "Oswald", sans-serif; letter-spacing: 2px; text-transform: uppercase; }

  .heart { position: absolute; left: 40px; top: 170px; width: 680px; height: 640px; overflow: visible; }
  .heart-shape { fill: var(--heart-red); stroke: #fff; stroke-width: 18; }
  .curved-claim { font: 600 21px "Oswald", sans-serif; fill: var(--ink); }

  .tagline {
    position: absolute; left: 130px; top: 262px; color: #fff;
    font: 42px "Kaushan Script", cursive; transform: rotate(-4deg);
  }
  .product-name {
    position: absolute; left: 0; right: 0; top: 345px; text-align: center;
    font: 900 64px/1 "Playfair Display", serif; letter-spacing: -2px;
    transform: scaleY(1.35); transform-origin: center top;
  }
  .product-name .low { color: #fff; }
  .product-name .carb { color: var(--ink); }
  .product-name .chips { color: var(--gold); }

  .flavor-badge {
    position: absolute; left: 160px; top: 444px; width: 100px; height: 48px;
    background: linear-gradient(180deg, #f0a52e, #d2333b); border-radius: 10px;
    color: #fff; font: 600 19px "Oswald", sans-serif; display: flex; align-items: center; justify-content: center;
  }
  .flavor-name { position: absolute; left: 274px; top: 444px; color: #fff; font: 400 32px/48px "Playfair Display", serif; }
  .high-protein { position: absolute; right: 125px; top: 500px; color: var(--ink); font: 900 26px "Playfair Display", serif; }

  .chips-photo {
    position: absolute; left: 185px; top: 540px; width: 300px; height: 230px; border-radius: 48% 52% 46% 54%;
    background: radial-gradient(circle at 45% 40%, var(--chip-light), var(--chip-deep));
  }
  .sour-cream-photo {
    position: absolute; left: 90px; top: 620px; width: 135px; height: 95px; border-radius: 50%;
    background: radial-gradient(circle at 50% 40%, #ffffff, #d7e6cf);
  }

  .protein-seal {
    position: absolute; left: 478px; top: 548px; width: 128px; height: 128px; border-radius: 50%;
    background: #fff; border: 5px solid var(--brand-red);
    display: flex; flex-direction: column; align-items: center; justify-content: center; color: var(--ink);
  }
  .protein-seal .amount { font: 600 38px/1 "Oswald", sans-serif; }
  .protein-seal .label { font: 600 18px/1.2 "Oswald", sans-serif; }

  .macro-list { position: absolute; left: 505px; top: 768px; display: flex; gap: 10px; }
  .macro {
    width: 50px; height: 50px; color: #fff; text-align: center;
    display: flex; flex-direction: column; justify-content: center;
  }
  .macro .macro-label { font: 500 8px/1 "Oswald", sans-serif; }
  .macro .macro-value { font: 700 17px/1.1 "Playfair Display", serif; }
  .macro.carbs { background: var(--carbs-green); }
  .macro.fat { background: var(--fat-teal); }
  .macro.sugar { background: var(--sugar-gold); }

  .weight-band {
    position: absolute; left: 210px; top: 840px; width: 340px; height: 80px;
    background: var(--brand-red); border-radius: 8px 8px 0 0;
    display: flex; align-items: center; justify-content: center; gap: 40px;
  }
  .natural-mark {
    width: 54px; height: 54px; border-radius: 50%; border: 2px solid #fff; color: #fff;
    display: flex; flex-direction: column; align-items: center; justify-content: center;
    font: 500 11px/1.1 "Oswald", sans-serif;
  }
  .net-weight { color: #fff; font: 700 48px "Playfair Display", serif; }
</style>
</head>
<body>
  <div class="bag">
    <div class="bag-pattern" role="img" aria-label="Repeating line-drawn pattern of chips and tortilla triangles"></div>

    <div class="brand-tab"><span class="brand-name">Munchvale</span></div>

    <svg class="heart" viewBox="0 0 680 640" aria-hidden="true">
      <path class="heart-shape" d="M340 625 C150 485 20 365 20 190 C20 80 110 10 210 10 C270 10 315 40 340 85 C365 40 410 10 470 10 C570 10 660 80 660 190 C660 365 530 485 340 625 Z"/>
      <path id="claim-arc" d="M400 -10 C520 -28 660 20 700 150" fill="none"/>
      <text class="curved-claim"><textPath href="#claim-arc">Snack Chips Rich Protein</textPath></text>
    </svg>

    <div class="tagline">Crispy &amp; Testy</div>
    <h1 class="product-name"><span class="low">LOW</span><span class="carb">CARB</span><span class="chips">CHIPS</span></h1>

    <div class="flavor-badge">FLAVOR</div>
    <div class="flavor-name">SOUR CREAM &amp; ONION</div>
    <div class="high-protein">HIGH PROTEIN</div>

    <div class="sour-cream-photo" role="img" aria-label="Bowl of sour cream topped with chopped chives"></div>
    <div class="chips-photo" role="img" aria-label="Pile of golden ridged potato chips"></div>

    <div class="protein-seal"><span class="amount">20G</span><span class="label">PROTEIN</span></div>

    <div class="macro-list">
      <div class="macro carbs"><span class="macro-label">CARBS</span><span class="macro-value">10G</span></div>
      <div class="macro fat"><span class="macro-label">FAT</span><span class="macro-value">10G</span></div>
      <div class="macro sugar"><span class="macro-label">SUGAR</span><span class="macro-value">30G</span></div>
    </div>

    <div class="weight-band">
      <div class="natural-mark"><span>100%</span><span>VEGAN</span></div>
      <span class="net-weight">80g</span>
    </div>
  </div>
</body>
</html>
```